Business Card Design

We are a manufacturing and distribution company with most of our customer base being supermarkets. We have established brand guidelines that are attached.

```html
<!DOCTYPE html>
<html lang="en">
<head>
<meta charset="utf-8">
<title>Corvane — Business Card</title>
<link rel="stylesheet" href="https://fonts.googleapis.com/css2?family=Arimo:wght@400;700&display=swap">
<style>
  :root {
    --bg: #c9c9c9;
    --paper: #ffffff;
    --brand-red: #e31d24;
    --brand-red-dark: #c8141b;
    --brand-blue: #1565b0;
    --ink: #1b1b1b;
    --rule: #d6d6d6;
  }
  * { margin: 0; padding: 0; box-sizing: border-box; }
  html, body { width: 1200px; height: 800px; overflow: hidden; }
  body {
    background: var(--bg);
    font-family: "Arimo", Arial, sans-serif;
    position: relative;
  }
  .card {
    position: absolute;
    top: 245px;
    width: 540px;
    height: 310px;
    box-shadow: 0 6px 18px rgba(0,0,0,0.18);
  }
  /* Front side */
  .card-front {
    left: 40px;
    background: var(--paper);
    border-bottom: 3px solid var(--brand-red);
  }
  .front-brand {
    position: absolute;
    left: 0; top: 0;
    width: 270px; height: 100%;
    display: flex;
    align-items: center;
    justify-content: center;
    gap: 12px;
  }
  .brand-square {
    width: 26px; height: 26px;
    background: var(--brand-red);
  }
  .brand-name {
    font-weight: 700;
    font-size: 34px;
    letter-spacing: 1px;
    color: var(--ink);
  }
  .front-divider {
    position: absolute;
    left: 270px; top: 70px;
    width: 1px; height: 170px;
    background: var(--rule);
  }
  .front-details {
    position: absolute;
    left: 296px; top: 62px;
    color: var(--ink);
  }
  .person-name {
    font-weight: 700;
    font-size: 21px;
    letter-spacing: 0.5px;
    text-transform: uppercase;
  }
  .person-first { color: var(--brand-red); }
  .person-last { color: var(--brand-blue); }
  .person-role {
    font-size: 14px;
    margin-top: 3px;
  }
  .contact-list {
    list-style: none;
    margin-top: 16px;
    font-size: 14px;
    line-height: 22px;
  }
  .contact-list li {
    display: flex;
    align-items: center;
    gap: 8px;
  }
  .contact-icon { width: 13px; height: 13px; flex: none; }
  .web-accent { color: var(--brand-blue); }
  .address {
    margin-top: 14px;
    font-size: 14px;
    line-height: 19px;
  }
  /* Back side */
  .card-back {
    left: 620px;
    overflow: hidden;
  }
  .back-field {
    position: absolute;
    inset: 0;
    background: linear-gradient(135deg, #ec3a3f 0%, var(--brand-red) 50%, var(--brand-red-dark) 100%);
  }
  .back-brand {
    position: absolute;
    inset: 0;
    display: flex;
    align-items: center;
    justify-content: center;
    gap: 14px;
  }
  .back-brand .brand-square { background: var(--paper); width: 30px; height: 30px; }
  .back-brand .brand-name { color: var(--paper); font-size: 38px; }
</style>
</head>
<body>
  <section class="card card-front">
    <div class="front-brand">
      <span class="brand-square"></span>
      <span class="brand-name">CORVANE</span>
    </div>
    <div class="front-divider"></div>
    <div class="front-details">
      <p class="person-name"><span class="person-first">Daniel</span> <span class="person-last">Moreau</span></p>
      <p class="person-role">Managing Director</p>
      <ul class="contact-list">
        <li>
          <svg class="contact-icon" viewBox="0 0 16 16"><circle cx="8" cy="8" r="8" fill="#e31d24"/><path d="M5 4.5c.6-.4 1.1-.3 1.4.3l.6 1.2c.2.4.1.8-.3 1.1l-.4.3c.4.9 1.1 1.6 2 2l.3-.4c.3-.4.7-.5 1.1-.3l1.2.6c.6.3.7.8.3 1.4-.6.8-1.6 1-2.6.5C6.8 10.3 5.7 9.2 4.9 7.5c-.5-1-.4-2.2.1-3z" fill="#fff"/></svg>
          044-987 654 321
        </li>
        <li>
          <svg class="contact-icon" viewBox="0 0 16 16"><rect x="0" y="2" width="16" height="12" fill="#e31d24"/><path d="M1 3.5l7 5 7-5" stroke="#fff" stroke-width="1.4" fill="none"/></svg>
          hello@corvanefoods.com
        </li>
        <li>
          <svg class="contact-icon" viewBox="0 0 16 16"><circle cx="8" cy="8" r="8" fill="#e31d24"/><g stroke="#fff" stroke-width="1" fill="none"><circle cx="8" cy="8" r="5"/><ellipse cx="8" cy="8" rx="2.2" ry="5"/><path d="M3 8h10M4 5.5h8M4 10.5h8"/></g></svg>
          <span>www.<span class="web-accent">corvanefoods</span>.com</span>
        </li>
      </ul>
      <p class="address">88, Harbour Trade Road<br>10234,Eastvale</p>
    </div>
  </section>

  <section class="card card-back">
    <div class="back-field" role="img" aria-label="Embossed repeating brand pattern in red tones"></div>
    <div class="back-brand">
      <span class="brand-square"></span>
      <span class="brand-name">CORVANE</span>
    </div>
  </section>
</body>
</html>
```